Moden - Mexicali - Flower Shop

brisapetals is looking for a cool web design that has a airy, clean, mexicali feel to it.

See attached images and links for idea of what we mean with the above.

please no templates.

Target Market(s)

Local flower shop in San Diego, California

Industry/Entity Type

Shop

Requirements
Must have
• see. brisapetals.shopnest.example - I did the site and logo...I love the logo - hate the site.

Going for this feel: http://www.platetalk.example/menucraft/archives/verdanos.php

I also attached another site I liked- I just feel like it may be to busy.

```html
<!DOCTYPE html>
<html lang="en">
<head>
<meta charset="utf-8">
<title>California Lillies – brisapetals</title>
<link rel="stylesheet" href="https://fonts.googleapis.com/css2?family=Alegreya:ital,wght@1,400&family=Cambo&family=Habibi&display=swap">
<style>
  :root{
    --page:#3a2250;
    --panel:#b9aac7;
    --gold:#d9b23a;
    --gold-soft:#e6c65a;
    --footer:#241034;
    --plum:#3a2150;
    --violet:#8a2fb0;
    --sale:#e8141e;
    --was:#1e6f55;
    --muted:#e4dbec;
    --ink:#1f1428;
    --cream:#f3eef6;
  }
  *{margin:0;padding:0;box-sizing:border-box}
  html,body{width:1095px;height:1200px;overflow:hidden}
  body{position:relative;background:var(--page);font-family:"Habibi",serif;color:var(--ink)}
  .abs{position:absolute}
  .nav a{position:absolute;font-family:"Alegreya",serif;font-style:italic;color:var(--gold-soft);text-decoration:none;line-height:1}
  .nav .home{left:176px;top:13px;font-size:25px}
  .nav .shop{left:157px;top:56px;font-size:39px}
  .nav .curated{left:103px;top:115px;font-size:25px}
  .nav .about{left:18px;top:163px;font-size:25px}

  .search{left:774px;top:17px;width:170px;height:22px;background:#7d6a8d;border-radius:3px;color:var(--cream);font-size:14px;line-height:22px;padding-left:5px}
  .search svg{position:absolute;right:6px;top:3px}
  .cart-sum{left:960px;top:14px;font-size:18px;color:var(--cream);word-spacing:8px}
  .cart-sum span{border-bottom:1px solid var(--cream)}
  .view-cart{left:988px;top:47px;font-size:18px;color:var(--cream)}

  .brand{left:380px;top:80px;width:335px;height:93px;border:1px solid var(--gold)}
  .brand-inner{position:absolute;left:5px;top:4px;right:5px;bottom:4px;background:#fff;display:flex;align-items:center;justify-content:center;gap:14px}
  .brand-dot{width:30px;height:30px;border-radius:50%;background:#c9c4c9}
  .brand-name{font-family:"Cambo",serif;font-size:26px;letter-spacing:5px;color:#6fae94}

  .panel-frame{left:147px;top:203px;width:802px;height:707px;border:1px solid var(--gold)}
  .panel{left:153px;top:208px;width:791px;height:696px;background:var(--panel)}
  .back{left:162px;top:220px;font-size:11px;color:var(--ink)}
  .thumbs{left:446px;top:230px;display:flex;align-items:center;gap:11px}
  .thumb{width:43px;height:48px}
  .t1{background:linear-gradient(135deg,#7a2a38,#c2435d)}
  .t2{background:linear-gradient(135deg,#8d8a7a,#e4537c)}
  .t3{background:linear-gradient(135deg,#6c6d73,#e6e6e3)}

  .photo{left:181px;top:318px;width:315px;height:316px;background:linear-gradient(150deg,#a18c68 0%,#e0a13a 45%,#efcf3a 60%,#b7a89a 100%)}
  .share-title{left:181px;top:664px;font-family:"Alegreya",serif;font-style:italic;font-size:25px;color:var(--ink)}
  .share{left:181px;top:709px;display:flex;gap:8px}
  .dot{width:20px;height:20px;border-radius:50%;background:#ece7f0}

  .title{left:540px;top:312px;font-family:"Cambo",serif;font-size:38px;color:var(--plum)}
  .vendor{left:544px;top:356px;font-size:23px;color:var(--muted)}
  .price{left:547px;top:398px;font-family:"Alegreya",serif;font-style:italic;font-size:32px;color:var(--sale)}
  .price s{color:var(--was);margin-left:10px}
  .size-label{left:547px;top:446px;font-family:"Alegreya",serif;font-style:italic;font-size:23px}
  .size-select{left:541px;top:485px;width:84px;height:17px;background:#f1eef3;border-radius:2px;font-size:12px;line-height:17px;padding-left:24px}
  .size-select svg{position:absolute;right:6px;top:6px}
  .add{left:545px;top:520px;display:flex;align-items:center;gap:12px}
  .add-circle{width:58px;height:58px;border-radius:50%;border:2px solid #d8d0de;background:#a79bb1;position:relative}
  .add-text{font-family:"Cambo",serif;font-size:19px;color:var(--violet)}
  .desc-head{left:547px;top:642px;font-family:"Cambo",serif;font-size:17px;font-weight:bold}
  .desc{left:547px;top:671px;font-size:16px;line-height:21.5px}

  .rule{left:0;top:934px;width:1095px;height:2px;background:#e9e2ee}
  .footer{left:0;top:936px;width:1095px;height:264px;background:var(--footer);color:var(--cream)}
  .col{position:absolute;top:47px;font-size:13.5px;line-height:18px;letter-spacing:.4px}
  .col h4{font-family:"Cambo",serif;font-size:15px;font-weight:bold}
  .c1{left:146px}.c2{left:437px}.c3{left:710px}
  .f-social{position:absolute;left:146px;top:156px;display:flex;gap:10px}
  .f-social .dot{width:21px;height:21px;background:#cfc7d5}
  .email{position:absolute;left:709px;top:127px;width:177px;height:21px;background:#6a5a78;color:var(--cream);font-size:14px;line-height:21px;padding-left:6px}
  .signup{position:absolute;left:896px;top:129px;font-size:14px;color:#bdb2c6}
  .copy{position:absolute;left:0;width:1095px;top:234px;text-align:center;font-size:14px;color:#a89cb3;letter-spacing:.5px}
</style>
</head>
<body>
  <nav class="nav">
    <a class="home">Home</a>
    <a class="shop">Shop</a>
    <a class="curated">Curated</a>
    <a class="about">About Us</a>
  </nav>

  <div class="abs search">Search Store
    <svg width="16" height="16" viewBox="0 0 16 16"><circle cx="6.5" cy="6.5" r="5" fill="none" stroke="#f3eef6" stroke-width="1.4"/><line x1="10.2" y1="10.2" x2="15" y2="15" stroke="#f3eef6" stroke-width="1.4"/></svg>
  </div>
  <div class="abs cart-sum"><span>0 items</span> <span>$0.0</span></div>
  <div class="abs view-cart">View Cart</div>

  <div class="abs brand"><div class="brand-inner"><span class="brand-dot"></span><span class="brand-name">BRISA PETALS</span></div></div>

  <div class="abs panel-frame"></div>
  <main class="abs panel"></main>

  <div class="abs back">◂ Back</div>
  <div class="abs thumbs">
    <svg width="8" height="14"><polygon points="8,0 0,7 8,14" fill="#2a1a34"/></svg>
    <div class="thumb t1" role="img" aria-label="Red roses bouquet"></div>
    <div class="thumb t2" role="img" aria-label="Pink gerbera bouquet"></div>
    <div class="thumb t3" role="img" aria-label="White calla lilies"></div>
    <svg width="8" height="14"><polygon points="0,0 8,7 0,14" fill="#2a1a34"/></svg>
  </div>

  <div class="abs photo" role="img" aria-label="Bouquet of orange and yellow lilies wrapped in kraft paper on burlap"></div>
  <div class="abs share-title">Share this product</div>
  <div class="abs share"><span class="dot"></span><span class="dot"></span><span class="dot"></span><span class="dot"></span><span class="dot"></span><span class="dot"></span></div>

  <h1 class="abs title">California Lillies</h1>
  <div class="abs vendor">brisapetals</div>
  <div class="abs price">$ 60.00 <s>$ 75.00</s></div>
  <div class="abs size-label">Size</div>
  <div class="abs size-select">Large
    <svg width="8" height="5"><polygon points="0,0 8,0 4,5" fill="#1f1428"/></svg>
  </div>
  <div class="abs add">
    <div class="add-circle"><svg width="58" height="58" style="position:absolute;left:-2px;top:-2px"><line x1="16" y1="29" x2="42" y2="29" stroke="#f5eef8" stroke-width="2"/><line x1="29" y1="16" x2="29" y2="42" stroke="#f5eef8" stroke-width="2"/></svg></div>
    <span class="add-text">Add To Cart</span>
  </div>
  <div class="abs desc-head">Description</div>
  <div class="abs desc">Feel the energy of these colorful Lillies.<br>15 - Blooms<br>30 - Blooms</div>

  <div class="abs rule"></div>
  <footer class="abs footer">
    <div class="col c1"><h4>Meet Brisa</h4>Based in Hillcrest, San Diego<br>We offer farm fresh, curated,<br>cool, and same day delivery<br>flower bouquets.</div>
    <div class="f-social"><span class="dot"></span><span class="dot"></span><span class="dot"></span></div>
    <div class="col c2"><h4>Reach Brisa</h4>2210 Jacaranda Street<br>San Diego, CA 92104<br>Email: hello@brisapetals.example<br>Phone: 619-555-0148</div>
    <div class="col c3"><h4>Newsletter</h4>We promise to only send you<br>good things like discounts!</div>
    <div class="email">your@email.com</div>
    <div class="signup">Sign up</div>
    <div class="copy">Copyright © 2014 brisapetals of San Diego.</div>
  </footer>
</body>
</html>
```